Business Card Design Project

Business Card
We are rebranding with a new logo
Industry/Entity Type
Business
Contact Information for Business Card
Dennis Morvale +61 487215963 dennis@quorv.com.au P.O. Box 872 Fernlow QLD 4309
Requirements
Must have
- Logo

```html
<!DOCTYPE html>
<html lang="en">
<head>
<meta charset="utf-8">
<title>Quorv International – Business Card</title>
<link href="https://fonts.googleapis.com/css2?family=Roboto:wght@400;700&family=Dancing+Script:wght@600&display=swap" rel="stylesheet">
<style>
  :root {
    --page-bg: #e6e6e6;
    --card-white: #f7f7f7;
    --blue-deep: #0a4a68;
    --blue-mid: #0077b0;
    --blue-bright: #00a2dd;
    --navy-text: #14506e;
    --ink: #1c1c1c;
    --accent-orange: #e8641e;
    --white: #ffffff;
  }
  * { margin: 0; padding: 0; box-sizing: border-box; }
  html, body {
    width: 1200px;
    height: 576px;
    overflow: hidden;
    background: var(--page-bg);
  }
  .canvas {
    position: relative;
    width: 1200px;
    height: 576px;
  }
  .card {
    position: absolute;
    top: 139px;
    width: 484px;
    height: 292px;
    border-radius: 14px;
  }
  .card--front {
    left: 82px;
    background: linear-gradient(90deg, var(--blue-deep) 0%, var(--blue-mid) 50%, var(--blue-bright) 100%);
  }
  .card--back {
    left: 602px;
    background: var(--card-white);
  }

  .brand {
    position: absolute;
    display: flex;
    flex-direction: column;
    align-items: center;
    font-family: "Roboto", sans-serif;
    font-weight: 700;
  }
  .brand__row {
    display: flex;
    align-items: center;
    gap: 10px;
  }
  .brand__dot {
    width: 16px;
    height: 16px;
    border-radius: 50%;
    background: var(--accent-orange);
  }
  .brand__name {
    font-size: 52px;
    line-height: 1;
    letter-spacing: 1px;
  }
  .brand__tagline {
    margin-top: 8px;
    font-size: 15px;
    letter-spacing: 2.6px;
  }
  .card--front .brand {
    left: 0;
    right: 0;
    top: 92px;
    color: var(--white);
  }
  .card--back .brand {
    left: 36px;
    top: 112px;
    color: var(--navy-text);
  }
  .card--back .brand__name { font-size: 40px; }
  .card--back .brand__tagline { font-size: 12.5px; letter-spacing: 2px; margin-top: 7px; }
  .card--back .brand__dot { width: 13px; height: 13px; }

  .contact {
    position: absolute;
    left: 242px;
    top: 96px;
  }
  .contact__name {
    font-family: "Dancing Script", cursive;
    font-weight: 600;
    font-size: 25px;
    color: var(--navy-text);
    margin-bottom: 14px;
  }
  .contact__list { list-style: none; }
  .contact__item {
    display: flex;
    align-items: center;
    gap: 10px;
    font-family: "Roboto", sans-serif;
    font-size: 12.5px;
    color: var(--ink);
    height: 17px;
  }
  .contact__icon {
    width: 11px;
    height: 11px;
    fill: var(--accent-orange);
    flex: none;
  }
</style>
</head>
<body>
<main class="canvas">
  <section class="card card--front" aria-label="Card front">
    <div class="brand">
      <div class="brand__row">
        <span class="brand__dot"></span>
        <span class="brand__name">Quorv</span>
      </div>
      <span class="brand__tagline">INTERNATIONAL</span>
    </div>
  </section>

  <section class="card card--back" aria-label="Card back">
    <div class="brand">
      <div class="brand__row">
        <span class="brand__dot"></span>
        <span class="brand__name">Quorv</span>
      </div>
      <span class="brand__tagline">INTERNATIONAL</span>
    </div>

    <div class="contact">
      <p class="contact__name">Dennis Morvale</p>
      <ul class="contact__list">
        <li class="contact__item">
          <svg class="contact__icon" viewBox="0 0 12 12" aria-hidden="true"><path d="M1 4.5C1 3 2.5 2 6 2s5 1 5 2.5v.8H8.6V4H3.4v1.3H1z M3 6h6l1.5 4.5h-9z"/></svg>
          +61 487215963
        </li>
        <li class="contact__item">
          <svg class="contact__icon" viewBox="0 0 12 12" aria-hidden="true"><path d="M0.5 2.5h11v7h-11z M1.2 3.2L6 6.8l4.8-3.6" stroke="#f7f7f7" stroke-width="0.9"/></svg>
          dennis@quorv.com.au
        </li>
        <li class="contact__item">
          <svg class="contact__icon" viewBox="0 0 12 12" aria-hidden="true"><path d="M6 0.5a4 4 0 0 1 4 4c0 3-4 7-4 7s-4-4-4-7a4 4 0 0 1 4-4zm0 2.3a1.7 1.7 0 1 0 0 3.4a1.7 1.7 0 0 0 0-3.4z"/></svg>
          P.O. Box 872 Fernlow QLD 4309
        </li>
      </ul>
    </div>
  </section>
</main>
</body>
</html>
```